Ashmoor Web Design Project

I need the front page and an internal page designed for this client's website. The logo is attached. Obviously the colors have to go with and/or work with the logo colors. I also attached a very rough brochure layout to help you see the direction we're going in with print materials. The rough site map is also attached. I see a slider on the homepage, the art for which I may come back to you to create. This clinic is in a very high end Dallas neighborhood. The hook is that it's a primary care and urgent facility with convenient hours.

I don't know how much this impacts your design, but this will be a Wordpress site and I'm using a framework called Brovila (brovila.com). If Brovila proves to be inflexible, I'll have to get a template that allows me to execute your design.

This site (http://lanternvaleclinic.com) has the type and quality of content I will eventually have on the Ashmoor site.

I just revised the brief for this project. I added the site map and added details to the overview and the "Must Have" section. Thank you for revisiting the brief. 

Reason: Christmas was a bad time to end it.

Target Market(s)

Women 25-54 with children living at home, income over $150k/year

Industry/Entity Type

Clinic

Requirements
Must have
• Masthead incorporating the logo
Followed by the primary nav
Slider on the home page below that
Dual nav - 1 with the nav in the attached site map
2 secondary nav with areas of healthcare
There will three blocks under the nav
1. It's about time (with a small blurb less than 50 words.
2. It's about choices (with small blurb)
3. It's about you (with small blurb)
Three footer blocks
patient check in link on every page
"No appointment? No problem" icon on every page

```html
<!DOCTYPE html>
<html lang="en">
<head>
<meta charset="utf-8">
<title>Ashmoor Medical</title>
<link href="https://fonts.googleapis.com/css2?family=Arimo:wght@400;700&family=Ubuntu:wght@400;500&display=swap" rel="stylesheet">
<style>
:root{
  --green:#1fc25c;
  --green-dark:#15a84a;
  --green-text:#18a94c;
  --blue:#0a5aa8;
  --blue-bar:#1b74d4;
  --text:#333;
  --muted:#444;
  --panel-blue:#e4e8f3;
  --panel-green:#ebfaf0;
  --band:#e6e9f4;
}
*{margin:0;padding:0;box-sizing:border-box}
html,body{width:1200px;height:1200px;overflow:hidden;background:#fff}
body{position:relative;font-family:"Arimo",Arial,sans-serif;color:var(--text);font-size:12px}
.abs{position:absolute}
.topbar{left:0;top:0;width:1200px;height:40px;background:linear-gradient(#2ee070,var(--green-dark));box-shadow:0 2px 3px rgba(0,0,0,.15)}
.mainnav{left:473px;top:0;height:40px;display:flex}
.mainnav a{display:block;height:40px;line-height:40px;text-align:center;color:#fff;font-weight:700;font-size:14px;text-decoration:none;border-left:1px solid rgba(255,255,255,.35);text-shadow:0 1px 1px rgba(0,0,0,.25)}
.mainnav a.current{background:#fff;color:var(--green-text);text-shadow:none;border-left:none}
.brand{left:132px;top:62px;display:flex;align-items:center;gap:8px}
.brand .dot{width:36px;height:36px;border-radius:50%;background:var(--blue)}
.brand .name{font-size:26px;font-weight:700;color:var(--blue);letter-spacing:-.5px}
.tagline{left:202px;top:92px;font-size:8px;font-weight:700;color:var(--blue)}
.userlinks{left:960px;top:69px;font-size:11px;color:var(--blue)}
.userlinks a{color:var(--blue);text-decoration:none}
.video-head{left:130px;top:158px;font-size:12px;font-weight:700;color:var(--muted)}
.video-thumb{left:129px;top:180px;width:182px;height:104px;background:linear-gradient(135deg,#8c8a6e,#c9c5b3 55%,#6e6a55)}
.video-time{right:6px;bottom:3px;color:#fff;font-size:11px;background:rgba(0,0,0,.5);padding:0 3px}
.video-blurb{left:130px;top:297px;width:175px;font-size:11px;line-height:13.3px;color:var(--muted)}
.slide-title{left:371px;top:174px;font-family:"Ubuntu",sans-serif;font-weight:400;font-size:24px;color:var(--blue)}
.slide-text{left:371px;top:205px;width:350px;font-family:"Ubuntu",sans-serif;font-size:12px;line-height:14.6px;color:var(--blue)}
.slide-dots{left:371px;top:300px;display:flex;gap:5px}
.slide-dots span{width:8px;height:8px;border-radius:50%;background:var(--green)}
.slide-dots span.on{background:#555}
.slide-art{left:755px;top:125px;width:290px;height:230px;border-radius:50% 45% 48% 50%;background:radial-gradient(circle at 50% 50%,#a8c8a8,#8fb58f)}
.band{left:0;top:378px;width:1200px;height:43px;background:linear-gradient(#fff,var(--band))}
.connect{left:131px;top:441px;font-size:12px;color:var(--muted)}
.social{left:131px;top:463px;display:flex;gap:7px}
.social span{width:24px;height:24px;border-radius:3px;background:#2a5aa0}
.contact{left:130px;top:520px;width:200px;font-size:12px;line-height:14.6px;color:#222}
.contact .site{font-weight:700}
.contact .addr{margin-top:10px}
.contact .phone{margin-top:14px;font-weight:700}
.panel{border-radius:4px;box-shadow:0 1px 3px rgba(0,0,0,.25);overflow:hidden}
.about{left:370px;top:402px;width:460px;height:270px;background:var(--panel-blue)}
.about .cap{height:18px;background:linear-gradient(#3a8ee6,var(--blue-bar))}
.about h2{margin:18px 0 0 20px;font-size:14px;color:var(--blue)}
.about p{margin:4px 20px 0 20px;font-size:12px;line-height:14.4px;color:#222}
.about .photo{position:absolute;left:20px;top:129px;width:418px;height:119px;background:linear-gradient(90deg,#d9d2c6,#eeece8 45%,#b9cfd8);border:1px solid #cfd4df}
.areas{left:850px;top:402px;width:220px;height:210px;background:var(--panel-green)}
.areas .cap{height:18px;background:linear-gradient(#2fd870,var(--green-dark))}
.areas h2{margin:18px 0 0 19px;font-size:14px;color:var(--green-text)}
.areas ul{list-style:none;margin:3px 0 0 30px}
.areas li{font-size:12px;font-weight:700;color:#555;height:19.4px;line-height:19.4px}
.areas li::before{content:"›";display:inline-block;width:20px;color:#333}
.checkin{left:861px;top:640px;display:flex;align-items:center;gap:10px;font-family:"Ubuntu",sans-serif;font-size:14px;color:var(--green-text);font-weight:500;text-decoration:none}
.checkin .icon{width:29px;height:29px;border-radius:50%;background:var(--green);display:flex;align-items:center;justify-content:center}
.blurb{top:701px;width:220px}
.blurb h3{font-size:11px;font-weight:700;color:var(--muted);padding-bottom:8px;border-bottom:1px solid var(--green)}
.blurb p{font-size:12px;line-height:14.2px;color:#222;margin-top:8px;padding-right:4px}
.blurb p.lead{text-indent:36px}
.footer-shade{left:140px;top:958px;width:920px;height:20px;background:radial-gradient(ellipse at 50% 0,rgba(0,0,0,.18),rgba(0,0,0,0) 70%)}
.footlinks{left:0;top:988px;width:1200px;text-align:center;font-size:11px;color:var(--blue)}
.footlinks a{color:var(--blue);text-decoration:none}
.copyright{left:0;top:1012px;width:1200px;text-align:center;font-size:11px;color:var(--blue)}
</style>
</head>
<body>
<div class="abs topbar"></div>
<nav class="abs mainnav">
  <a class="current" href="#" style="width:60px">Home</a><a href="#" style="width:89px">About</a><a href="#" style="width:95px">Services</a><a href="#" style="width:72px">Staff</a><a href="#" style="width:104px">Insurance</a><a href="#" style="width:83px">Videos</a><a href="#" style="width:114px">Contact Us</a>
</nav>

<div class="abs brand"><span class="dot"></span><span class="name">Ashmoor Medical</span></div>
<div class="abs tagline">Everyday Care Close to Home</div>
<div class="abs userlinks"><a href="#">Register</a> | <a href="#">Login</a> | <a href="#">Blog</a></div>

<div class="abs video-head">View our intro video &gt;</div>
<div class="abs video-thumb" role="img" aria-label="Intro video still: doctor in a clinic room">
  <svg class="abs" style="left:148px;top:41px" width="24" height="24" viewBox="0 0 24 24"><circle cx="12" cy="12" r="11" fill="#333" stroke="#fff" stroke-width="1.5"/><path d="M9.5 7l7 5-7 5z" fill="#fff"/></svg>
  <span class="abs video-time">2:19</span>
</div>
<p class="abs video-blurb">Lorem ipsum dolor sit amet, consectetur adipiscing elit. Donec dolor arcu, accumsan nec auctor vitae, elementum et augue.</p>

<h1 class="abs slide-title">Title of Slide One</h1>
<p class="abs slide-text">Lorem ipsum dolor sit amet, consectetur adipiscing elit. Duis ac euismod urna. Praesent in arcu feugiat justo fringilla luctus. Sed nisi odio, pharetra vel commodo nec, auctor a est.</p>
<div class="abs slide-dots"><span class="on"></span><span></span><span></span><span></span></div>
<div class="abs slide-art" role="img" aria-label="Illustration of a doctor checking a seated patient with a stethoscope"></div>

<div class="abs band"></div>

<div class="abs connect">Connect with us</div>
<div class="abs social"><span></span><span></span><span></span></div>
<div class="abs contact">
  <div class="site">AshmoorFamilyMedical.com</div>
  <div class="addr">4720 Marlow Ave (at<br>Preston Rd) Ste 210,<br>Dallas, TX 75209</div>
  <div class="phone">(214) 555 0142</div>
</div>

<section class="abs panel about">
  <div class="cap"></div>
  <h2>About Ashmoor Medical</h2>
  <p>Lorem ipsum dolor sit amet, consectetur adipiscing elit. Donec dolor arcu, accumsan nec auctor vitae, elementum et augue. Aliquam erat volutpat. Sed blandit placerat nibh vel dignissim. Nullam ac lacus eu est feugiat lobortis eu vitae leo. Ut ornare ante nec mauris fermentum pretium.</p>
  <div class="photo" role="img" aria-label="Photo of smiling doctors with nursing staff in the background"></div>
</section>

<section class="abs panel areas">
  <div class="cap"></div>
  <h2>Practice Areas:</h2>
  <ul>
    <li>Immediate Care</li><li>Allergies</li><li>Primary Care</li><li>Women’s Health</li><li>Medical Spa Treatments</li><li>Men’s Health</li><li>Weight Loss</li>
  </ul>
</section>

<a class="abs checkin" href="#"><span class="icon"><svg width="16" height="18" viewBox="0 0 16 18"><rect x="2" y="2" width="12" height="15" rx="1" fill="none" stroke="#fff" stroke-width="1.6"/><rect x="5" y="0.5" width="6" height="3" fill="#fff"/><path d="M5 9h6M5 12h6" stroke="#fff" stroke-width="1.4"/></svg></span>Patient Check In &gt;</a>

<section class="abs blurb" style="left:370px">
  <h3>IT’S ABOUT TIME</h3>
  <p class="lead">Lorem ipsum dolor sit amet, consectetur adipiscing elit. Sed ut risus a massa varius viverra. In hac habitasse platea dictumst. Quisque faucibus pulvinar mi et luctus.</p>
  <p>Duis lacus augue, malesuada sed dignissim ut, tincidunt quis ante. Nunc ultrices odio ac elit tempor.</p>
</section>
<section class="abs blurb" style="left:610px">
  <h3>IT’S ABOUT TIME</h3>
  <p class="lead">Lorem ipsum dolor sit amet, consectetur adipiscing elit. Sed ut risus a massa varius viverra. In hac habitasse platea dictumst. Quisque faucibus pulvinar mi et luctus.</p>
  <p>Duis lacus augue, malesuada sed dignissim ut, tincidunt quis ante. Nunc ultrices odio ac elit tempor.</p>
</section>
<section class="abs blurb" style="left:850px">
  <h3>IT’S ABOUT TIME</h3>
  <p class="lead">Lorem ipsum dolor sit amet, consectetur adipiscing elit. Sed ut risus a massa varius viverra. In hac habitasse platea dictumst. Quisque faucibus pulvinar mi et luctus.</p>
  <p>Duis lacus augue, malesuada sed dignissim ut, tincidunt quis ante. Nunc ultrices odio ac elit tempor.</p>
</section>

<div class="abs footer-shade"></div>
<div class="abs footlinks"><a href="#">Insurance &amp; Billing</a> | <a href="#">FAQ</a> | <a href="#">Sitemap</a> | <a href="#">Contact Us</a> | <a href="#">Legal Disclaimer</a> | <a href="#">Privacy Policy</a></div>
<div class="abs copyright">Copyright ©2012 Ashmoor Medical, All rights reserved.</div>
</body>
</html>
```